Flat bootstrap design for existing site

I'm looking for a modern flat design based around an existing logo. This has to be a custom design (no external templates), and implemented into a bootstrap framework.

The logo is attached as 2 versions - choose whichever you want, that flows better with whatever design you choose.

Added screenshots of the existing site (currently using the default bootstrap layouts). Please make your designs around those pages in the screenshots (i.e. the homepage only has the postal code input and the header). The active page has 3 screenshots, because I wanted to illustrate the other states that would be visible (in the table rows).

This is a moving/junk removal website, just for some context.

Here's some example websites (flat designs) that I like, just to give you an idea of what I'm after.

https://www.plimvora.com/
https://dacklow.com/
https://trevanu.com/
https://quobrintal.com/en/

Coding

Coded - Design and coding required

Number of Pages Required

5+ page

Colors

Designer to choose colors to be used in the design.

Requirements
Must have
• It must be a modern/simple flat design, that is built around the existing logo (attached).
• It has to be implemented using bootstrap.

```html
<!DOCTYPE html>
<html lang="en">
<head>
<meta charset="utf-8">
<title>Haulvix – Active Booking</title>
<link href="https://fonts.googleapis.com/css2?family=Open+Sans:wght@400;600;700&display=swap" rel="stylesheet">
<style>
  :root{
    --brand:#4bc8f4;
    --brand-dark:#41b4dc;
    --white:#ffffff;
    --panel:#f4f4f4;
    --panel-border:#dcdcdc;
    --row-alt:#e6e6e6;
    --text:#222222;
    --pending:#777777;
    --input-border:#cfcfcf;
  }
  *{box-sizing:border-box;margin:0;padding:0}
  html,body{width:1200px;height:974px;overflow:hidden;background:var(--white)}
  body{font-family:"Open Sans",sans-serif;color:var(--text);position:relative}
  .site-header{position:absolute;left:0;top:0;width:1200px;height:81px;background:var(--brand)}
  .brand{position:absolute;left:99px;top:22px;display:flex;align-items:center;gap:10px;color:var(--white);font-weight:700;font-size:30px;letter-spacing:1px;line-height:36px}
  .brand-dot{width:22px;height:22px;border-radius:50%;background:var(--white)}
  .main-nav a{position:absolute;top:0;height:81px;line-height:79px;color:var(--white);text-decoration:none;font-weight:700;font-size:15px}
  .nav-book{left:458px}
  .nav-how{left:555px}
  .nav-driver{left:697px;width:191px;background:var(--brand-dark);text-align:center}
  .nav-account{left:915px;font-weight:600!important;font-size:15.5px!important}
  .caret{position:absolute;left:1091px;top:38px}
  .booking-panel{position:absolute;left:99px;top:122px;width:1002px;height:396px;background:var(--panel);border:2px solid var(--panel-border);border-radius:3px}
  .panel-title{position:absolute;left:19px;top:21px;color:var(--brand);font-weight:700;font-size:21px;line-height:28px}
  .field-label{position:absolute;font-weight:600;font-size:15.5px;line-height:21px}
  .field{position:absolute;background:var(--white);border:2px solid var(--input-border);border-radius:3px;font-size:14px;padding:0 12px;line-height:35px}
  .field svg{position:absolute;right:10px;top:11px}
  .btn-update{position:absolute;left:21px;top:323px;width:110px;height:39px;background:var(--brand);color:var(--white);border:0;border-radius:3px;font:600 15.5px "Open Sans",sans-serif;letter-spacing:.5px}
  .section-title{position:absolute;left:98px;top:552px;color:var(--brand);font-weight:700;font-size:24px;line-height:32px}
  .notice{position:absolute;left:99px;top:605px;width:1002px;height:48px;background:var(--brand);color:var(--white);font-weight:600;font-size:15px;line-height:48px;padding-left:15px}
  .drivers-table{position:absolute;left:99px;top:684px;width:1002px;border:2px solid var(--panel-border);border-radius:3px;border-collapse:separate;border-spacing:0;overflow:hidden}
  .drivers-table th{background:var(--brand);color:var(--white);font-weight:600;font-size:15.5px;text-align:left;height:50px;padding-left:16px}
  .drivers-table td{height:48px;padding-left:16px;font-weight:600;font-size:14.5px;background:var(--panel)}
  .drivers-table tr:nth-child(even) td{background:var(--row-alt)}
  .col-name{width:188px}.col-dist{width:189px}.col-time{width:231px}
  .status{display:inline-block;width:116px;height:30px;line-height:30px;text-align:center;background:var(--pending);color:var(--white);font-size:14.5px;font-weight:600}
</style>
</head>
<body>
  <header class="site-header">
    <div class="brand"><span class="brand-dot"></span>HAULVIX</div>
    <nav class="main-nav">
      <a class="nav-book" href="#">BOOK</a>
      <a class="nav-how" href="#">HOW IT WORKS</a>
      <a class="nav-driver" href="#">BECOME A DRIVER</a>
      <a class="nav-account" href="#">sam4@mailvent.com</a>
    </nav>
    <svg class="caret" width="10" height="6" viewBox="0 0 10 6"><path d="M0 0h10L5 6z" fill="#fff"/></svg>
  </header>

  <section class="booking-panel">
    <h2 class="panel-title">Booking Details:</h2>
    <label class="field-label" style="left:19px;top:82px">Package selected:</label>
    <div class="field" style="left:21px;top:118px;width:461px;height:39px">Package 1
      <svg width="9" height="16" viewBox="0 0 9 16"><path d="M4.5 1L8 6H1zM4.5 15L8 10H1z" fill="#333"/></svg>
    </div>
    <label class="field-label" style="left:516px;top:82px">Pick-up time selected:</label>
    <div class="field" style="left:518px;top:118px;width:461px;height:39px">July 18 at 4:13 am
      <svg width="13" height="14" viewBox="0 0 13 14"><rect x="0.5" y="2" width="12" height="11.5" fill="none" stroke="#333"/><rect x="0.5" y="2" width="12" height="3" fill="#333"/><path d="M3 4.5 3 0.5M10 4.5V0.5" stroke="#333"/><path d="M1 8h11M1 11h11M4 5v8M6.5 5v8M9 5v8" stroke="#333" stroke-width=".6"/></svg>
    </div>
    <label class="field-label" style="left:19px;top:176px">Description:</label>
    <div class="field" style="left:21px;top:212px;width:958px;height:90px;line-height:24px;padding-top:6px">1 large stove</div>
    <button class="btn-update">UPDATE</button>
  </section>

  <h2 class="section-title">Drivers in your area</h2>
  <p class="notice">Please stay on this page and be patient, while we contact the drivers and find you one ASAP.</p>

  <table class="drivers-table">
    <thead>
      <tr><th class="col-name">Name</th><th class="col-dist">Distance (km)</th><th class="col-time">Agreed pick-up time</th><th></th></tr>
    </thead>
    <tbody>
      <tr><td>Derek Halm</td><td>4.04km away</td><td>-</td><td><span class="status">Pending</span></td></tr>
      <tr><td>Marcus Bell</td><td>5.7km away</td><td>-</td><td><span class="status">Pending</span></td></tr>
      <tr><td>Owen Prater</td><td>11.13km away</td><td>-</td><td><span class="status">Pending</span></td></tr>
      <tr><td>Glen Rowley</td><td>11.91km away</td><td>-</td><td><span class="status">Pending</span></td></tr>
    </tbody>
  </table>
</body>
</html>
```